SaaS Early tech startup business card design

Unique design for experience ecommerce platform company. the business cards will be used by executive members. conformance with color code is required.

```html
<!DOCTYPE html>
<html lang="en">
<head>
<meta charset="utf-8">
<title>Velto Business Card</title>
<link href="https://fonts.googleapis.com/css2?family=Archivo:wght@400;700;800&display=swap" rel="stylesheet">
<style>
  :root {
    --stage: #2a2a2e;
    --card: #23233d;
    --teal: #1db39a;
    --teal-deep: #178c8a;
    --ink: #ffffff;
    --rule: #d8d8e4;
  }
  * { margin: 0; padding: 0; box-sizing: border-box; }
  html, body {
    width: 1200px; height: 900px; overflow: hidden;
    background: var(--stage);
    font-family: "Archivo", Arial, sans-serif;
  }
  .canvas {
    position: relative; width: 1200px; height: 900px;
  }
  .card {
    position: absolute; left: 260px; width: 680px; height: 390px;
    background: var(--card);
    border-radius: 26px;
    box-shadow: 0 14px 30px rgba(0,0,0,0.45);
    overflow: hidden;
  }
  .card-front { top: 45px; }
  .card-back { top: 465px; }

  .brand-name {
    color: var(--teal);
    font-weight: 800;
    letter-spacing: 1px;
    line-height: 1;
  }
  .card-front .brand-name {
    position: absolute; left: 0; right: 0; top: 145px;
    text-align: center; font-size: 104px;
  }
  .card-back .brand-name {
    position: absolute; right: 46px; top: 40px;
    font-size: 78px;
  }

  .divider {
    position: absolute; left: 46px; right: 46px; top: 222px;
    height: 1.5px; background: var(--rule);
  }
  .person {
    position: absolute; left: 46px; top: 158px;
  }
  .person-name {
    color: var(--teal); font-weight: 800; font-size: 31px;
    letter-spacing: 0.5px; line-height: 1.1;
  }
  .person-role {
    color: var(--ink); font-size: 22px; line-height: 1.2;
  }
  .address {
    position: absolute; right: 46px; top: 160px;
    color: var(--ink); font-size: 21px; line-height: 1.3; text-align: right;
  }

  .contact-list {
    position: absolute; left: 46px; top: 244px;
    list-style: none;
  }
  .contact-list .short-rule {
    width: 330px; height: 1.5px; background: var(--rule); margin-bottom: 14px;
  }
  .contact-item {
    display: flex; align-items: center; gap: 14px;
    color: var(--ink); font-size: 23px; margin-bottom: 8px;
  }
  .contact-icon { width: 28px; height: 28px; flex: none; }
</style>
</head>
<body>
<div class="canvas">

  <section class="card card-front">
    <div class="brand-name">Velto</div>
  </section>

  <section class="card card-back">
    <div class="brand-name">Velto</div>

    <div class="person">
      <div class="person-name">Marcus Hale</div>
      <div class="person-role">Manager</div>
    </div>

    <div class="address">Your address, city<br>state, ZIP 0000</div>

    <div class="divider"></div>

    <ul class="contact-list">
      <li class="short-rule"></li>
      <li class="contact-item">
        <svg class="contact-icon" viewBox="0 0 28 28" aria-hidden="true">
          <rect width="28" height="28" rx="6" fill="var(--teal)"/>
          <path d="M9 7c1 0 2 2.5 2.3 3.5.2.8-1.3 1.5-1 2.3.8 2 2.4 3.6 4.4 4.4.8.3 1.5-1.2 2.3-1 1 .3 3.5 1.3 3.5 2.3 0 1.5-1.5 2.8-3 2.5C11.5 20 8 16.5 6.5 10c-.3-1.5 1-3 2.5-3z" fill="#fff"/>
        </svg>
        <span>555-014-7382</span>
      </li>
      <li class="contact-item">
        <svg class="contact-icon" viewBox="0 0 28 28" aria-hidden="true">
          <rect width="28" height="28" rx="6" fill="var(--teal)"/>
          <rect x="6" y="8.5" width="16" height="11" rx="1" fill="none" stroke="#fff" stroke-width="1.8"/>
          <path d="M6.5 9.5 14 15l7.5-5.5" fill="none" stroke="#fff" stroke-width="1.8"/>
        </svg>
        <span>youremail@mailhub.com</span>
      </li>
      <li class="contact-item">
        <svg class="contact-icon" viewBox="0 0 28 28" aria-hidden="true">
          <rect width="28" height="28" rx="6" fill="var(--teal)"/>
          <circle cx="14" cy="14" r="7.5" fill="none" stroke="#fff" stroke-width="1.8"/>
          <ellipse cx="14" cy="14" rx="3.2" ry="7.5" fill="none" stroke="#fff" stroke-width="1.5"/>
          <path d="M6.5 14h15" stroke="#fff" stroke-width="1.5"/>
        </svg>
        <span>www.yourwebsite.com</span>
      </li>
    </ul>
  </section>

</div>
</body>
</html>
```